Landscape Construction and Design Company

We are a landscape construction and design company from New Jersey. We design and install landscapes and hardscapes for residential properties. The name of the company is Belwick's Landscape and Design LLC. We specialize mostly in planting trees and stone work, some water features. We would like to see design themes that include a tree or trees and a stone walkway or wall. We like earth tone colors. We like traditional to modern designs.

Target Market(s)

Homeowners

Industry/Entity Type

Landscape

Contact Information for Business Card

Nature themed design, earth tone colors, space for company name, address, phone numbers, email and website address

Logo Text

No text

Font styles to use
Serif

Colors

Designer to choose colors to be used in the design.

Requirements
Must have
• A tree or trees, similar to the ones uploaded in my supporting images
Nice to have
• I like trees similar to those in my uploaded supporting images. I like artistic, nature theme, earth tone colors
Should not have
• Pictures of real landscapes, cartoon looking logo or objects

```html
<!DOCTYPE html>
<html lang="en">
<head>
<meta charset="utf-8">
<title>Belwick's Landscape and Design LLC – Business Card</title>
<link href="https://fonts.googleapis.com/css2?family=Cinzel:wght@400;600&family=PT+Sans:wght@400;700&display=swap" rel="stylesheet">
<style>
  :root {
    --backdrop: #3b322e;
    --card: #f7f7f5;
    --card-back: #f1f1f0;
    --leaf-green: #6aa72f;
    --trunk-brown: #7a2a24;
    --ink: #1e1e1e;
    --rule: #a9a9a9;
  }
  * { margin: 0; padding: 0; box-sizing: border-box; }
  html, body {
    width: 1200px; height: 844px; overflow: hidden;
    background: var(--backdrop);
  }
  .stage {
    position: relative; width: 1200px; height: 844px;
    display: flex; align-items: center; justify-content: center; gap: 40px;
  }
  .card {
    position: relative; width: 540px; height: 309px;
    background: var(--card);
    box-shadow: 0 6px 18px rgba(0,0,0,.35);
  }
  .card--back { background: var(--card-back); display: flex; align-items: center; justify-content: center; }

  .wordmark {
    position: absolute; top: 34px; left: 230px;
    display: flex; align-items: center; gap: 12px;
  }
  .wordmark__dot {
    width: 46px; height: 46px; border-radius: 50%;
    background: var(--leaf-green);
  }
  .wordmark__name {
    font-family: "Cinzel", serif; font-weight: 400;
    color: var(--leaf-green); font-size: 15px; line-height: 1.25;
    width: 220px;
  }
  .back-mark {
    display: flex; flex-direction: column; align-items: center; gap: 14px;
  }
  .back-mark__dot { width: 120px; height: 120px; border-radius: 50%; background: var(--leaf-green); }
  .back-mark__name {
    font-family: "Cinzel", serif; font-weight: 400; color: var(--leaf-green); font-size: 16px;
  }

  .rule { position: absolute; height: 1px; background: var(--rule); right: 24px; }
  .rule--1 { top: 104px; left: 228px; }
  .rule--2 { top: 142px; left: 228px; }
  .rule--3 { top: 196px; left: 24px; }
  .rule--4 { top: 230px; left: 24px; }
  .rule--5 { top: 264px; left: 24px; }

  .contact {
    position: absolute; left: 28px;
    font-family: "PT Sans", sans-serif; font-size: 15px; color: var(--ink);
  }
  .contact .label { color: var(--leaf-green); font-weight: 700; margin-right: 4px; }
  .person { top: 150px; }
  .person__name {
    font-family: "Cinzel", serif; font-weight: 600; color: var(--leaf-green);
    font-size: 17px; letter-spacing: .5px; line-height: 1;
  }
  .person__title { font-size: 15px; line-height: 1.2; }
  .address { top: 205px; }
  .phone-row { top: 239px; display: flex; gap: 18px; width: 484px; }
  .phone-row .web { margin-left: auto; color: var(--leaf-green); font-weight: 700; font-size: 13px; }
  .services {
    top: 275px; color: var(--leaf-green); font-size: 16px; letter-spacing: .3px;
  }
  .services .sep { color: var(--trunk-brown); margin: 0 4px; }
</style>
</head>
<body>
<main class="stage">
  <section class="card card--front" aria-label="Business card front">
    <div class="wordmark">
      <span class="wordmark__dot"></span>
      <span class="wordmark__name">Belwick's Landscape and Design LLC</span>
    </div>
    <div class="rule rule--1"></div>
    <div class="rule rule--2"></div>
    <div class="contact person">
      <p class="person__name">DANIEL HART</p>
      <p class="person__title">Managing Director</p>
    </div>
    <div class="rule rule--3"></div>
    <p class="contact address">48 Orchard Lane, Montclair, NJ 07042</p>
    <div class="rule rule--4"></div>
    <p class="contact phone-row">
      <span><span class="label">P:</span>(201) 555-0148</span>
      <span><span class="label">E:</span>info@belwicks.com</span>
      <span class="web">www.belwicks.com</span>
    </p>
    <div class="rule rule--5"></div>
    <p class="contact services">PLANTING TREES<span class="sep">|</span>STONE WORK<span class="sep">|</span>WATER FEATURES</p>
  </section>

  <section class="card card--back" aria-label="Business card back">
    <div class="back-mark">
      <span class="back-mark__dot"></span>
      <span class="back-mark__name">Belwick's Landscape and Design LLC</span>
    </div>
  </section>
</main>
</body>
</html>
```